BrimFalcon Business Cards

We have a defined brand. Please visit our website to get a feel for the product and the color pallets. www.brimfalcon-example.com

We need an updated, world class business card design. (See the attached existing card design). Please utilize BOTH sides of the card as shown and be creative with the layout. I do want the horse head icon to be positioned as it is with the existing card.

The remainder of the layout can be customized and I also want it vertically oriented.

Attached are the logo files and please use the colors as follows:
Green - #A5CE39
Tan - #CDBD99
Black

Feel free to play with the colors.

```html
<!DOCTYPE html>
<html lang="en">
<head>
<meta charset="utf-8">
<title>BrimFalcon Labs — Business Card</title>
<link href="https://fonts.googleapis.com/css2?family=Montserrat:wght@400;500;600&display=swap" rel="stylesheet">
<style>
  :root {
    --backdrop: #2a2a2b;
    --card: #1c1c1d;
    --card-edge: #101011;
    --text: #f2f2f2;
    --green: #a5ce39;
    --green-deep: #5fa83a;
    --mark-dim: #3a3a3c;
  }
  * { box-sizing: border-box; margin: 0; padding: 0; }
  html, body {
    width: 1200px; height: 900px; overflow: hidden;
    background: var(--backdrop);
    font-family: "Montserrat", sans-serif;
  }
  .sheet {
    width: 1200px; height: 900px;
    display: flex; align-items: center; justify-content: center; gap: 60px;
  }
  .card {
    width: 525px; height: 300px;
    background: var(--card);
    border: 1px solid var(--card-edge);
    border-radius: 3px;
    box-shadow: 0 14px 30px rgba(0,0,0,.45);
    position: relative;
    overflow: hidden;
  }
  /* Front */
  .card-front { display: flex; align-items: center; padding: 0 26px; }
  .brand { width: 212px; flex: none; }
  .brand-lockup { display: flex; align-items: center; gap: 8px; }
  .brand-dot { width: 18px; height: 18px; border-radius: 50%; background: var(--text); flex: none; }
  .brand-name { font-size: 20px; font-weight: 600; color: var(--text); letter-spacing: .3px; white-space: nowrap; }
  .brand-tagline { margin-top: 6px; padding-left: 26px; font-size: 10px; color: var(--text); letter-spacing: 1.8px; white-space: nowrap; }
  .divider { width: 1px; height: 150px; background: var(--green-deep); margin: 0 18px 0 12px; flex: none; }
  .contact { color: var(--text); font-size: 12px; line-height: 1.5; min-width: 0; }
  .contact-name { font-size: 17px; font-weight: 600; color: var(--green); letter-spacing: .5px; line-height: 1.25; white-space: nowrap; }
  .contact-title { margin-bottom: 6px; }
  .contact-place { margin-bottom: 8px; }
  .contact-line { display: flex; align-items: center; gap: 6px; white-space: nowrap; }
  .contact-line svg { width: 11px; height: 11px; flex: none; }
  /* Back */
  .card-back { display: flex; align-items: center; justify-content: center; gap: 14px; }
  .back-dot { width: 30px; height: 30px; border-radius: 50%; background: var(--mark-dim); }
  .back-name { font-size: 34px; font-weight: 600; color: var(--mark-dim); letter-spacing: .5px; }
</style>
</head>
<body>
<main class="sheet">
  <section class="card card-front" aria-label="Card front">
    <div class="brand">
      <div class="brand-lockup">
        <span class="brand-dot"></span>
        <span class="brand-name">BrimFalcon Labs</span>
      </div>
      <p class="brand-tagline">Performance Driven EVs</p>
    </div>
    <div class="divider"></div>
    <div class="contact">
      <p class="contact-name">OWEN STRAKE</p>
      <p class="contact-title">President &amp; CEO</p>
      <p class="contact-place">Aldenmoor, Saskatchewan<br>Canada</p>
      <p class="contact-line">
        <svg viewBox="0 0 12 12"><path fill="#a5ce39" d="M2.5 1h2l1 2.6-1.3.9a6.5 6.5 0 0 0 3.3 3.3l.9-1.3 2.6 1v2A1.5 1.5 0 0 1 9.5 11 8.5 8.5 0 0 1 1 2.5 1.5 1.5 0 0 1 2.5 1z"/></svg>
        306.555.0142
      </p>
      <p class="contact-line">
        <svg viewBox="0 0 12 12"><rect x="1" y="2.5" width="10" height="7" rx="1" fill="#a5ce39"/><path d="M1.5 3l4.5 3.5L10.5 3" fill="none" stroke="#1c1c1d" stroke-width="1"/></svg>
        owen@brimfalcon-example.com
      </p>
      <p class="contact-line">
        <svg viewBox="0 0 12 12"><circle cx="6" cy="6" r="4.6" fill="none" stroke="#a5ce39" stroke-width="1.2"/><path d="M1.5 6h9M6 1.4c-2.2 2.6-2.2 6.6 0 9.2M6 1.4c2.2 2.6 2.2 6.6 0 9.2" fill="none" stroke="#a5ce39" stroke-width=".9"/></svg>
        BrimFalconLabs-example.com
      </p>
    </div>
  </section>

  <section class="card card-back" aria-label="Card back">
    <span class="back-dot"></span>
    <span class="back-name">BrimFalcon</span>
  </section>
</main>
</body>
</html>
```